Business Card design for law firm = Brightvale Australia

We are seeking a new design for our business cards.
We are keeping our logo, which is attached.
We need space for
Name
Title
Address is , which is
Level 7
214 Marlowe Street
Sydney NSW 2047
Phone :
Mobile :
Fax :
Email :
DX :
website www.brightvale-example.com.au

Industry/Entity Type

Law Firm / Banking and Finance

Contact Information for Business Card

We are seeking a new design for our business cards. We are keeping our logo. We need space for Name Title Address is Level 7 214 Marlowe Street Sydney NSW 2047 Phone Mobile Fax Email DX website www.brightvale-example.com.au

Colors
0054AA
0677BA
7BADD7
CADEEF
E8F1F8

Requirements
Must have
• see our website for general feel www.brightvale-example.com.au

```html
<!DOCTYPE html>
<html lang="en">
<head>
<meta charset="utf-8">
<title>Brightvale Australia – Business Card</title>
<link href="https://fonts.googleapis.com/css2?family=Crimson+Pro:wght@500&family=Open+Sans:wght@400&family=Arimo:wght@400;700&display=swap" rel="stylesheet">
<style>
  :root {
    --navy: #0054AA;
    --blue: #0677BA;
    --sky: #0AA0DC;
    --mid: #7BADD7;
    --ink: #1a1a1a;
    --paper: #ffffff;
    --stage: #2b2b2b;
  }
  * { margin: 0; padding: 0; box-sizing: border-box; }
  html, body { width: 1200px; height: 1108px; overflow: hidden; background: var(--stage); }
  .stage { position: relative; width: 1200px; height: 1108px; }
  .card {
    position: absolute; top: 214px; width: 400px; height: 660px;
    border-radius: 22px; overflow: hidden;
    box-shadow: 0 14px 30px rgba(0,0,0,.45);
  }
  .card--front { left: 160px; background: var(--paper); }
  .card--back { left: 640px; background: var(--blue); }

  .brand { position: absolute; left: 0; right: 0; text-align: center; }
  .front__brand { top: 150px; }
  .brand__name { font-family: "Crimson Pro", serif; font-weight: 500; font-size: 62px; line-height: 1; color: var(--blue); letter-spacing: .5px; }
  .brand__tagline { font-family: "Open Sans", sans-serif; font-size: 19px; letter-spacing: 2px; color: var(--sky); margin-top: 8px; }

  .person { position: absolute; top: 330px; left: 0; right: 0; text-align: center; }
  .person__name { font-family: "Crimson Pro", serif; font-weight: 500; font-size: 32px; line-height: 1.05; color: var(--blue); }
  .person__title { font-family: "Arimo", sans-serif; font-size: 17px; color: var(--sky); margin-top: 2px; }
  .rule { width: 100px; height: 1px; background: var(--ink); margin: 12px auto; }

  .contact { font-family: "Arimo", sans-serif; font-size: 16px; line-height: 1.42; color: var(--ink); }
  .contact b { color: var(--blue); font-weight: 700; }
  .contact .web { color: var(--blue); }
  .address { font-family: "Arimo", sans-serif; font-size: 16px; line-height: 1.4; color: var(--ink); }

  .back__field { position: absolute; inset: 0; background: linear-gradient(200deg, #1596e0 0%, var(--blue) 45%, #0563a3 100%); }
  .back__brand { top: 470px; }
  .back__brand .brand__name, .back__brand .brand__tagline { color: var(--paper); }
</style>
</head>
<body>
<main class="stage">
  <section class="card card--front" aria-label="Business card front">
    <div class="brand front__brand">
      <div class="brand__name">Brightvale</div>
      <div class="brand__tagline">banking and finance lawyers</div>
    </div>
    <div class="person">
      <div class="person__name">Daniel Hartley</div>
      <div class="person__title">Managing Director</div>
      <div class="rule"></div>
      <div class="contact">
        <div><b>P:</b> 044-987 654 321</div>
        <div><b>M:</b> 044-987 654 321</div>
        <div><b>F:</b> 044-987 654 321</div>
        <div><b>E:</b> info@brightvale-example.com.au</div>
        <div><b>DX</b> :000987654321</div>
        <div>www.<span class="web">brightvale-example</span>.com.au</div>
      </div>
      <div class="rule"></div>
      <div class="address">
        <div>Level 7, 214 Marlowe Street</div>
        <div>Sydney NSW 2047</div>
      </div>
    </div>
  </section>

  <section class="card card--back" aria-label="Business card back">
    <div class="back__field" role="img" aria-label="Blue background where a faint repeating decorative pattern belongs"></div>
    <div class="brand back__brand">
      <div class="brand__name">Brightvale</div>
      <div class="brand__tagline">banking and finance lawyers</div>
    </div>
  </section>
</main>
</body>
</html>
```